New Business Card Design Project

Need a design that will create an impact / strong impression towards our clients for our business. We are in the lighting business and we do lighting retrofits for large commercial to industrial clientele.

Target Market(s)

Lighting Industry

Industry/Entity Type

Business

Font styles to use
Other font styles liked:
• we would like to use the font on our logo, not sure what it is though..

Requirements
Must have
• Our logo.
Nice to have
• We are open to suggestions that have to do with lighting.

```html
<!DOCTYPE html>
<html lang="en">
<head>
<meta charset="utf-8">
<title>Lumen Retrofit Co. – Business Card</title>
<link href="https://fonts.googleapis.com/css2?family=Montserrat:wght@400;500;600&display=swap" rel="stylesheet">
<style>
  :root {
    --bg: #1c1c1c;
    --card: #262626;
    --card-edge: #2c2c2c;
    --green: #5cc04a;
    --green-deep: #1f8f45;
    --white: #f2f2f2;
    --muted: #9a9a9a;
  }
  * { margin: 0; padding: 0; box-sizing: border-box; }
  html, body {
    width: 1200px; height: 900px; overflow: hidden;
    background: var(--bg);
    font-family: "Montserrat", Arial, sans-serif;
  }
  .stage {
    position: relative; width: 1200px; height: 900px;
    display: flex; flex-direction: column; align-items: center; justify-content: center; gap: 40px;
  }
  .card {
    position: relative; width: 630px; height: 360px;
    background: linear-gradient(135deg, var(--card) 0%, var(--card-edge) 100%);
    box-shadow: 0 18px 40px rgba(0,0,0,.55);
    overflow: hidden;
  }
  .card__stripe {
    position: absolute; left: 0; right: 0; bottom: 0; height: 7px;
    background: var(--green);
  }

  /* front */
  .card--front .brand {
    position: absolute; top: 130px; left: 0; right: 0;
    display: flex; align-items: center; justify-content: center; gap: 14px;
  }
  .card--front .brand__name {
    font-size: 34px; font-weight: 600; letter-spacing: 2px; color: #bdbdbd;
  }
  .card--front .brand__mark { width: 18px; height: 18px; background: #bdbdbd; }
  .card--front .web {
    position: absolute; bottom: 44px; left: 0; right: 0; text-align: center;
    font-size: 14px; letter-spacing: 2px; color: var(--white);
  }
  .card--front .web span { color: var(--green); }

  /* back */
  .card--back .brand {
    position: absolute; top: 140px; left: 40px;
    display: flex; align-items: center; gap: 12px;
  }
  .card--back .brand__mark { width: 16px; height: 16px; background: var(--green); }
  .card--back .brand__name {
    font-size: 26px; font-weight: 600; letter-spacing: 1px; color: var(--white);
  }
  .divider {
    position: absolute; left: 330px; top: 90px; width: 1px; height: 140px;
    background: var(--green-deep);
  }
  .person { position: absolute; left: 360px; top: 96px; }
  .person__name {
    font-size: 24px; font-weight: 500; letter-spacing: 1.5px; color: var(--green-deep);
    text-transform: uppercase;
  }
  .person__role { font-size: 18px; color: var(--white); margin-top: 2px; }
  .contacts { list-style: none; margin-top: 20px; }
  .contacts li {
    display: flex; align-items: center; gap: 14px;
    font-size: 15px; letter-spacing: .8px; color: var(--white); margin-bottom: 8px;
  }
  .contacts svg { width: 13px; height: 13px; flex: none; }
  .address {
    position: absolute; left: 0; right: 0; bottom: 40px; text-align: center;
    font-size: 16px; letter-spacing: 1px; color: var(--white);
  }
</style>
</head>
<body>
<main class="stage">
  <section class="card card--front">
    <div class="brand">
      <span class="brand__name">Lumen Retrofit Co.</span>
      <span class="brand__mark"></span>
    </div>
    <p class="web">www.<span>lumenretrofit</span>.com</p>
    <div class="card__stripe"></div>
  </section>

  <section class="card card--back">
    <div class="brand">
      <span class="brand__name">Lumen Retrofit Co.</span>
      <span class="brand__mark"></span>
    </div>
    <div class="divider"></div>
    <div class="person">
      <h1 class="person__name">Daniel Reyes</h1>
      <p class="person__role">Founder</p>
      <ul class="contacts">
        <li>
          <svg viewBox="0 0 24 24" aria-hidden="true"><path fill="#1f8f45" d="M6.6 10.8a15 15 0 0 0 6.6 6.6l2.2-2.2a1 1 0 0 1 1-.25 11.4 11.4 0 0 0 3.6.57 1 1 0 0 1 1 1V20a1 1 0 0 1-1 1A17 17 0 0 1 3 4a1 1 0 0 1 1-1h3.5a1 1 0 0 1 1 1c0 1.25.2 2.45.57 3.57a1 1 0 0 1-.25 1z"/></svg>
          0400 555 019
        </li>
        <li>
          <svg viewBox="0 0 24 24" aria-hidden="true"><rect x="2" y="5" width="20" height="14" fill="#1f8f45"/><path d="M2 5l10 8 10-8" fill="none" stroke="#262626" stroke-width="2"/></svg>
          info@lumenretrofit.com
        </li>
        <li>
          <svg viewBox="0 0 24 24" aria-hidden="true"><g fill="none" stroke="#1f8f45" stroke-width="2"><circle cx="12" cy="12" r="10"/><ellipse cx="12" cy="12" rx="4" ry="10"/><path d="M2 12h20"/></g></svg>
          www.lumenretrofit.com
        </li>
      </ul>
    </div>
    <p class="address">4410 West Canyon Road, Suite A204 Tempe AZ 85281</p>
    <div class="card__stripe"></div>
  </section>
</main>
</body>
</html>
```